MES Modul-Struktur grafisch veranschaulichen
Zielgruppe
Wir sind Software-Hersteller. Thema 'MES'. Unsere Kunden sind Produktionsunternehmen.
Mit einem MES (Manufacturing Execution System) werden Produktionsprozesse überwacht, geplant, gesteuert und optimiert. Allgemein geht es darum, die Produktivität zu steigern und Kosten zu minimieren.
Eine MES-Software ist modular strukturiert, so dass der Kunde sich nach Bedarf die einzelnen Funktionsmodule zusammenstellen kann. Unser MES KORVIN 7 MAX besteht z.B. aus folgenden Einzelmodulen:
- BASIS (Basismodul)
- MDE (Maschinendatenerfassung)
- BDE (Betriebsdatenerfassung)
- INST (Instandhaltung)
- ALARM (Alarmierung)
- DOK (Dokumentenmanagement)
- TNT (Traceability)
- PLAN (Feinplanung/Leitstand)
- LOG (Logistik)
- VIS (Visualisierung)
- PEP (Personaleinsatzplanung)
- MPZE (Personalzeiterfassung)
- DNC (Rezepturen/DNC)
- EM (Energiemonitoring)
Aufgabenstellung
Die modulare Struktur und der große Umfang an Modulen ist ein wichtiger Vorteil für unsere Kunden, da Sie nicht so schnell an Grenzen stoßen und sich dann unter Umständen eine weitere Insellösung (extra Software mit extra Datenbank ...) anschaffen müssen.
Wichtig ist, dass die einzelnen Module funktionell ineinandergreifen und alle auf die gleiche Datenbank zugreifen.
Es reicht wenn in der Grafik die Module nur mit er Abkürzung, also z.B. MDE bezeichnet werden. Für den ersten Entwurf können auch Platzhalter genutzt werden.
Der Betrachter sollte aus der Grafik auf den ersten Blick erkennen:
- umfängliches MES
- modular strukturiert
- Funktionsmodule step-by-step erweiterbar
Für die Umsetzung naheliegend wären Puzzle-Steine, Blokkis, ... muss aber nicht.

```html
<!DOCTYPE html>
<html lang="de">
<head>
<meta charset="utf-8">
<title>MES Modul-Struktur</title>
<link rel="stylesheet" href="https://fonts.googleapis.com/css2?family=Source+Sans+3:wght@400;700&display=swap">
<style>
  :root {
    --bg: #ffffff;
    --ink: #111111;
    --ring: #cccccc;
    --divider: #ffffff;
    --core: #000000;
    --basis: #9e7039;
    --mde: #ff4a00;
    --bde-green: #80ff00;
    --bde: #4dd8ff;
    --inst: #8b0090;
    --alarm: #ff0000;
    --mde-lime: #ccff00;
    --dok: #0000ee;
    --tnt: #22cc00;
    --plan: #9c6b35;
    --log: #ff7a70;
    --vis: #6fdcff;
    --pep: #bf5a5a;
    --mpze: #e0b48e;
    --dnc: #eecb72;
    --em: #f5f0a0;
    --extra: #f2a5f5;
  }
  html, body {
    margin: 0;
    padding: 0;
    width: 1200px;
    height: 848px;
    overflow: hidden;
    background: var(--bg);
  }
  .canvas { display: block; width: 1200px; height: 848px; }
  .diagram-title {
    font-family: "Source Sans 3", sans-serif;
    font-size: 22px;
    fill: var(--ink);
  }
  .ring { fill: var(--ring); }
  .divider { stroke: var(--divider); stroke-width: 4; }
  .product-label {
    font-family: "Source Sans 3", sans-serif;
    font-size: 23px;
    fill: #ffffff;
    text-anchor: middle;
  }
  .module-label {
    font-family: "Source Sans 3", sans-serif;
    font-weight: 700;
    font-size: 18px;
    fill: #ffffff;
    text-anchor: middle;
  }
  .module-label.small { font-size: 14px; }
  .core { fill: var(--core); }
  .core-label {
    font-family: "Source Sans 3", sans-serif;
    font-weight: 700;
    font-size: 19px;
    fill: #ffffff;
    text-anchor: middle;
    letter-spacing: -0.5px;
  }
  .m-basis { fill: var(--basis); }
  .m-mde { fill: var(--mde); }
  .m-bde-green { fill: var(--bde-green); }
  .m-bde { fill: var(--bde); }
  .m-inst { fill: var(--inst); }
  .m-alarm { fill: var(--alarm); }
  .m-mde-lime { fill: var(--mde-lime); }
  .m-dok { fill: var(--dok); }
  .m-tnt { fill: var(--tnt); }
  .m-plan { fill: var(--plan); }
  .m-log { fill: var(--log); }
  .m-vis { fill: var(--vis); }
  .m-pep { fill: var(--pep); }
  .m-mpze { fill: var(--mpze); }
  .m-dnc { fill: var(--dnc); }
  .m-em { fill: var(--em); }
  .m-extra { fill: var(--extra); }
</style>
</head>
<body>
<svg class="canvas" viewBox="0 0 1750 1237" xmlns="http://www.w3.org/2000/svg" xmlns:xlink="http://www.w3.org/1999/xlink">
  <defs>
    <g id="module-wedge">
      <path d="M0 0 L-22.07 -193.75 A195 195 0 0 1 22.07 -193.75 Z" stroke="#ffffff" stroke-width="3" stroke-linejoin="round"/>
      <line x1="0" y1="0" x2="-7.38" y2="-194.86" stroke="#ffffff" stroke-width="2.5"/>
      <line x1="0" y1="0" x2="7.38" y2="-194.86" stroke="#ffffff" stroke-width="2.5"/>
      <path d="M-22.07 -193.75 L-33.73 -296.1 A298 298 0 0 1 33.73 -296.1 L22.07 -193.75 A195 195 0 0 0 -22.07 -193.75 Z" stroke="#ffffff" stroke-width="3" stroke-linejoin="round"/>
    </g>
    <g id="product-ring">
      <circle class="ring" r="257"/>
      <line class="divider" x1="0" y1="0" x2="0" y2="-257" transform="rotate(52)"/>
      <line class="divider" x1="0" y1="0" x2="0" y2="-257" transform="rotate(125)"/>
      <line class="divider" x1="0" y1="0" x2="0" y2="-257" transform="rotate(232)"/>
      <line class="divider" x1="0" y1="0" x2="0" y2="-257" transform="rotate(304)"/>
    </g>
    <g id="customer-core">
      <circle class="core" r="35" stroke="#ffffff" stroke-width="2"/>
      <text class="core-label" y="7">KUNDE</text>
    </g>
  </defs>

  <!-- Basis Modul -->
  <text class="diagram-title" x="362" y="63" text-anchor="middle">Basis Modul</text>
  <g class="diagram" transform="translate(366 390)">
    <use href="#product-ring"/>
    <text class="product-label" x="-82" y="-130">Prod xy</text>
    <text class="product-label" x="74" y="-133">Prod 1</text>
    <text class="product-label" x="154" y="6">Prod 2</text>
    <text class="product-label" x="2" y="120">Prod 3</text>
    <text class="product-label" x="-130" y="10">Prod 4</text>
    <g transform="rotate(0)"><use href="#module-wedge" class="m-basis"/><text class="module-label" y="-275">BASIS</text></g>
    <use href="#customer-core"/>
  </g>

  <!-- Basis + 2 Module -->
  <text class="diagram-title" x="951" y="63" text-anchor="middle">Basis + 2 Module</text>
  <g class="diagram" transform="translate(914 390)">
    <use href="#product-ring"/>
    <text class="product-label" x="-76" y="-130">Prod xy</text>
    <text class="product-label" x="160" y="6">Prod 2</text>
    <text class="product-label" x="8" y="120">Prod 3</text>
    <text class="product-label" x="-124" y="10">Prod 4</text>
    <g transform="rotate(0)"><use href="#module-wedge" class="m-basis"/><text class="module-label" y="-275">BASIS</text></g>
    <g transform="rotate(13)"><use href="#module-wedge" class="m-mde"/><text class="module-label" y="-275">MDE</text></g>
    <g transform="rotate(26)"><use href="#module-wedge" class="m-bde-green"/><text class="module-label" y="-275">BDE</text></g>
    <use href="#customer-core"/>
  </g>

  <!-- Basis + 3 Module -->
  <text class="diagram-title" x="1503" y="63" text-anchor="middle">Basis + 3 Module</text>
  <g class="diagram" transform="translate(1464 392)">
    <use href="#product-ring"/>
    <text class="product-label" x="-74" y="-132">Prod xy</text>
    <text class="product-label" x="162" y="4">Prod 2</text>
    <text class="product-label" x="10" y="118">Prod 3</text>
    <text class="product-label" x="-122" y="8">Prod 4</text>
    <g transform="rotate(0)"><use href="#module-wedge" class="m-basis"/><text class="module-label" y="-275">BASIS</text></g>
    <g transform="rotate(13)"><use href="#module-wedge" class="m-mde"/><text class="module-label" y="-275">MDE</text></g>
    <g transform="rotate(26)"><use href="#module-wedge" class="m-bde"/><text class="module-label" y="-275">BDE</text></g>
    <g transform="rotate(39)"><use href="#module-wedge" class="m-inst"/><text class="module-label" y="-275">INST</text></g>
    <use href="#customer-core"/>
  </g>

  <!-- Basis + ... -->
  <text class="diagram-title" x="300" y="752">Basis + ...</text>
  <g class="diagram" transform="translate(607 917)">
    <use href="#product-ring"/>
    <text class="product-label" x="-72" y="-130">Prod xy</text>
    <text class="product-label" x="-120" y="10">Prod 4</text>
    <g transform="rotate(0)"><use href="#module-wedge" class="m-basis"/><text class="module-label" y="-275">BASIS</text></g>
    <g transform="rotate(13)"><use href="#module-wedge" class="m-mde"/><text class="module-label" y="-275">MDE</text></g>
    <g transform="rotate(26)"><use href="#module-wedge" class="m-bde"/><text class="module-label" y="-275">BDE</text></g>
    <g transform="rotate(39)"><use href="#module-wedge" class="m-inst"/><text class="module-label" y="-275">INST</text></g>
    <g transform="rotate(52)"><use href="#module-wedge" class="m-alarm"/><text class="module-label small" y="-276">ALARM</text></g>
    <g transform="rotate(65)"><use href="#module-wedge" class="m-mde-lime"/><text class="module-label" y="-275">MDE</text></g>
    <g transform="rotate(78)"><use href="#module-wedge" class="m-dok"/><text class="module-label" y="-275">DOK</text></g>
    <g transform="rotate(91)"><use href="#module-wedge" class="m-tnt"/><text class="module-label" y="-275">TNT</text></g>
    <g transform="rotate(104)"><use href="#module-wedge" class="m-plan"/><text class="module-label" y="-275">PLAN</text></g>
    <g transform="rotate(117)"><use href="#module-wedge" class="m-log"/></g>
    <g transform="rotate(130)"><use href="#module-wedge" class="m-vis"/></g>
    <g transform="rotate(143)"><use href="#module-wedge" class="m-pep"/></g>
    <g transform="rotate(156)"><use href="#module-wedge" class="m-mpze"/></g>
    <g transform="rotate(169)"><use href="#module-wedge" class="m-dnc"/></g>
    <g transform="rotate(182)"><use href="#module-wedge" class="m-em"/></g>
    <g transform="rotate(195)"><use href="#module-wedge" class="m-extra"/></g>
    <use href="#customer-core"/>
  </g>
</svg>
</body>
</html>
```